Danielle Brooke Interiors business cards

We need a DOUBLE SIDED business card design that is simple, elegant and modern. We are a rapidly growing Interior Design Firm, and our brand colours are blush pink, navy, and antique gold, so we require some or all of these colours to be used. The final design should portray elegance, simplicity, and have a modern feel. We have upload inspiration photos that have the feel we're looking for.

Industry/Entity Type

Interior Design

Contact Information for Business Card

Contact information and LOGO

Colors
EB3D1F
EC4F4E
F09395
F8D3D4
FCEDEE

Requirements
Must have
• Navy, the right shade of blush pink, and antique gold

```html
<!DOCTYPE html>
<html lang="en">
<head>
<meta charset="utf-8">
<title>Danielle Brooke Interiors – Business Cards</title>
<link href="https://fonts.googleapis.com/css2?family=Abril+Fatface&family=Jost:wght@400;500&display=swap" rel="stylesheet">
<style>
  :root {
    --backdrop: #dcd6e8;
    --navy: #1f2370;
    --gold: #b8902f;
    --white: #ffffff;
    --blush: #f5b3ad;
    --blush-light: #fcedee;
    --sky: #a9d6f2;
    --lavender: #b8a8d6;
    --sun: #f6d44a;
  }
  * { margin: 0; padding: 0; box-sizing: border-box; }
  html, body {
    width: 1200px;
    height: 1200px;
    overflow: hidden;
    background: var(--backdrop);
  }
  .canvas {
    position: relative;
    width: 1200px;
    height: 1200px;
  }
  .card {
    position: absolute;
    left: 312px;
    width: 558px;
    height: 318px;
    background: var(--white);
    box-shadow: 0 3px 8px rgba(40, 30, 70, 0.18);
    overflow: hidden;
  }
  .card--front { top: 256px; }
  .card--back  { top: 626px; }

  .pattern-fill {
    position: absolute;
    background:
      radial-gradient(circle at 30% 25%, var(--sky) 0, rgba(169,214,242,0) 45%),
      radial-gradient(circle at 70% 40%, var(--blush) 0, rgba(245,179,173,0) 45%),
      radial-gradient(circle at 55% 85%, var(--lavender) 0, rgba(184,168,214,0) 50%),
      var(--blush-light);
  }
  .card--front .pattern-fill { left: 0; top: 0; width: 280px; height: 100%; }
  .card--back .pattern-fill { inset: 0; }

  .front-details {
    position: absolute;
    left: 325px;
    top: 50px;
    color: var(--navy);
  }
  .holder-name {
    font-family: "Abril Fatface", serif;
    font-size: 40px;
    line-height: 37px;
    font-weight: 400;
  }
  .holder-role {
    margin-top: 38px;
    font-family: "Jost", sans-serif;
    font-size: 15px;
    letter-spacing: 0.2em;
    color: var(--gold);
  }
  .contact-list {
    list-style: none;
    margin-top: 38px;
    font-family: "Jost", sans-serif;
    font-size: 14px;
    line-height: 23px;
    letter-spacing: 0.08em;
  }

  .brand-frame {
    position: absolute;
    left: 91px;
    top: 57px;
    width: 376px;
    height: 202px;
    border: 4px solid var(--navy);
  }
  .brand-panel {
    position: absolute;
    left: 102px;
    top: 68px;
    width: 354px;
    height: 181px;
    background: var(--white);
    display: flex;
    align-items: center;
    justify-content: center;
    gap: 12px;
  }
  .brand-square {
    width: 14px;
    height: 14px;
    background: var(--blush);
  }
  .brand-name {
    font-family: "Jost", sans-serif;
    font-weight: 400;
    font-size: 18px;
    letter-spacing: 0.04em;
    text-transform: uppercase;
    color: var(--gold);
  }
</style>
</head>
<body>
<main class="canvas">
  <section class="card card--front">
    <div class="pattern-fill" role="img" aria-label="Abstract brushstroke pattern in blush, sky blue, lavender, navy and yellow"></div>
    <div class="front-details">
      <h1 class="holder-name">Danielle<br>Brooke</h1>
      <p class="holder-role">INTERIOR DESIGNER</p>
      <ul class="contact-list">
        <li>555-014-2230</li>
        <li>info@daniellebrooke.com</li>
        <li>www.daniellebrooke.com</li>
      </ul>
    </div>
  </section>

  <section class="card card--back">
    <div class="pattern-fill" role="img" aria-label="Abstract brushstroke pattern in blush, sky blue, lavender, navy and yellow"></div>
    <div class="brand-frame"></div>
    <div class="brand-panel">
      <span class="brand-square"></span>
      <span class="brand-name">Danielle Brooke Interiors</span>
    </div>
  </section>
</main>
</body>
</html>
```